Telvo Website - endlich neu?!
Aufgabenstellung
Es geht um die Gestaltung der Startseite auf Basis unseres verwendeten Magento-Templates.
Außerdem um die Gestaltung von Visitenkarte und Briefkopf.

```html
<!DOCTYPE html>
<html lang="de">
<head>
<meta charset="utf-8">
<title>Telvo – Die Jackenerweiterung</title>
<link rel="stylesheet" href="https://fonts.googleapis.com/css2?family=Bangers&family=Arimo:wght@400;700&display=swap">
<style>
  :root {
    --red: #ee1c1c;
    --red-dark: #c40000;
    --red-light: #ff4a4a;
    --text-gray: #555555;
    --footer-gray: #bcbcbc;
    --panel-gray: #f2f2f2;
    --frame-gray: #e4e4e4;
    --white: #ffffff;
    --ink: #111111;
  }
  * { box-sizing: border-box; margin: 0; padding: 0; }
  html, body { width: 1200px; height: 1128px; overflow: hidden; background: var(--white); }
  body { position: relative; font-family: "Arimo", Arial, sans-serif; color: var(--text-gray); }
  .abs { position: absolute; }

  .brand { left: 130px; top: 14px; font-family: "Arimo", Arial, sans-serif; font-weight: 700; font-size: 64px; line-height: 1; color: var(--ink); letter-spacing: -1px; }
  .tagline { left: 66px; top: 98px; font-size: 17px; font-weight: 700; color: var(--ink); }

  .like-button { left: 737px; top: 11px; width: 94px; height: 26px; border: 1px solid #9aa9c8; border-radius: 3px; background: linear-gradient(#fff, #eceef5); font-size: 12px; color: #3b5998; display: flex; align-items: center; justify-content: center; }
  .account-panel { left: 850px; top: 0; width: 310px; height: 46px; background: var(--panel-gray); border-radius: 0 0 20px 20px; display: flex; justify-content: center; align-items: center; gap: 6px; font-size: 13px; color: var(--ink); }

  .main-nav { left: 44px; top: 124px; width: 1116px; height: 48px; border-radius: 7px; border: 1px solid var(--red-dark); background: linear-gradient(var(--red-light), var(--red) 55%, var(--red-dark)); }
  .nav-item { top: 9px; font-family: "Bangers", "Arial Black", sans-serif; font-size: 23px; color: var(--white); letter-spacing: 1px; text-shadow: 1px 2px 2px rgba(0,0,0,.55); }
  .flag { top: 10px; width: 36px; height: 27px; }

  .hero-photo { left: 44px; top: 209px; width: 846px; height: 414px; background: linear-gradient(120deg, #e8e2da 0%, #6e1f2b 35%, #a9495a 55%, #141414 75%, #6f6a5e 100%); }
  .hero-claim { left: 535px; top: 418px; font-family: "Bangers", sans-serif; font-size: 40px; color: var(--white); line-height: .95; text-shadow: 1px 2px 3px rgba(0,0,0,.6); }
  .hero-claim span { display: block; font-size: 28px; padding-left: 50px; }
  .thumb { left: 908px; width: 252px; height: 127px; }
  .thumb-a { top: 209px; background: linear-gradient(120deg, #d9d3cc, #7a2333 45%, #181818); }
  .thumb-b { top: 353px; background: linear-gradient(90deg, #7a2333, #d6c3b8 40%, #7d7a5d 70%, #2a2a2a); }
  .thumb-c { top: 496px; background: linear-gradient(90deg, #7a2333, #d6c3b8 40%, #7d7a5d 70%, #2a2a2a); }

  .section-title { top: 656px; font-size: 24px; color: var(--text-gray); }
  .pager { top: 658px; width: 28px; height: 28px; }

  .product-card { top: 702px; width: 252px; height: 252px; border: 6px solid var(--frame-gray); background: linear-gradient(90deg, #1a1a1a 0%, #2b2b2b 40%, #b01c2a 50%, #ead2c4 65%, #f6f6f6 100%); }
  .product-name { top: 964px; font-size: 19px; color: var(--red); }

  .site-footer { left: 44px; top: 1056px; width: 1116px; height: 48px; background: var(--footer-gray); border-radius: 6px; font-size: 14px; color: var(--white); }
  .site-footer .abs { top: 15px; }
  .newsletter-input { left: 188px; top: 10px !important; width: 250px; height: 28px; border-radius: 14px; background: var(--white); color: #c8c8c8; font-size: 13px; padding: 6px 12px; }
  .divider { width: 1px; height: 48px; background: #d8d8d8; top: 0 !important; }
  .footer-links { left: 467px; display: flex; gap: 11px; }
</style>
</head>
<body>
  <div class="abs brand">Telvo</div>
  <div class="abs tagline">Die Jackenerweiterung!</div>

  <div class="abs like-button">Gefällt mir</div>
  <div class="abs account-panel"><span>Einloggen</span><span>Registrieren</span><span>Wunschliste</span></div>

  <nav class="abs main-nav">
    <span class="abs nav-item" style="left:25px">Start</span>
    <span class="abs nav-item" style="left:127px">Was ist Telvo?</span>
    <span class="abs nav-item" style="left:326px">Rund um Telvo</span>
    <span class="abs nav-item" style="left:535px">Shop</span>
    <span class="abs nav-item" style="left:631px">Händler</span>
    <svg class="abs flag" style="left:1004px" viewBox="0 0 36 27" role="img" aria-label="Englisch">
      <rect width="36" height="27" fill="#fff"/>
      <g fill="#c8102e"><rect y="0" width="36" height="3"/><rect y="6" width="36" height="3"/><rect y="12" width="36" height="3"/><rect y="18" width="36" height="3"/><rect y="24" width="36" height="3"/></g>
      <rect width="16" height="15" fill="#2a3b8f"/>
    </svg>
    <svg class="abs flag" style="left:1062px" viewBox="0 0 36 27" role="img" aria-label="Deutsch">
      <rect width="36" height="9" fill="#000"/><rect y="9" width="36" height="9" fill="#dd0000"/><rect y="18" width="36" height="9" fill="#ffce00"/>
    </svg>
  </nav>

  <div class="abs hero-photo" role="img" aria-label="Foto: Baby mit Mütze schläft warm eingepackt unter der Jacke mit Jackenerweiterung"></div>
  <div class="abs hero-claim">Wohlig warm<span>...auf dem Arm</span></div>
  <div class="abs thumb thumb-a" role="img" aria-label="Vorschaubild: Baby unter Jackenerweiterung"></div>
  <div class="abs thumb thumb-b" role="img" aria-label="Vorschaubild: Eltern mit Baby in Jacke"></div>
  <div class="abs thumb thumb-c" role="img" aria-label="Vorschaubild: Eltern mit Baby in Jacke"></div>

  <h2 class="abs section-title" style="left:44px;font-weight:400">Neue Produkte</h2>
  <svg class="abs pager" style="left:205px" viewBox="0 0 28 28"><circle cx="14" cy="14" r="13" fill="var(--red)" stroke="#f3a0a0"/><path d="M16.5 9 L10.5 14 L16.5 19 Z" fill="#fff"/></svg>
  <svg class="abs pager" style="left:240px" viewBox="0 0 28 28"><circle cx="14" cy="14" r="13" fill="var(--red)" stroke="#f3a0a0"/><path d="M11.5 9 L17.5 14 L11.5 19 Z" fill="#fff"/></svg>
  <h2 class="abs section-title" style="left:624px;font-weight:400">Beliebte Produkte</h2>
  <svg class="abs pager" style="left:814px" viewBox="0 0 28 28"><circle cx="14" cy="14" r="13" fill="var(--red)" stroke="#f3a0a0"/><path d="M16.5 9 L10.5 14 L16.5 19 Z" fill="#fff"/></svg>
  <svg class="abs pager" style="left:849px" viewBox="0 0 28 28"><circle cx="14" cy="14" r="13" fill="var(--red)" stroke="#f3a0a0"/><path d="M11.5 9 L17.5 14 L11.5 19 Z" fill="#fff"/></svg>

  <div class="abs product-card" style="left:44px" role="img" aria-label="Produktfoto: Hände ziehen roten Reißverschluss einer schwarzen Jackenerweiterung"></div>
  <div class="abs product-card" style="left:332px" role="img" aria-label="Produktfoto: Standardadapter mit Reißverschluss"></div>
  <div class="abs product-card" style="left:620px" role="img" aria-label="Produktfoto: Jackenerweiterung mit Reißverschluss"></div>
  <div class="abs product-card" style="left:908px" role="img" aria-label="Produktfoto: Jackenerweiterung mit Reißverschluss"></div>
  <div class="abs product-name" style="left:46px">Jackernerweiterung Schwarz</div>
  <div class="abs product-name" style="left:333px">Standardadapter (Zusatz)</div>
  <div class="abs product-name" style="left:623px">Jackenerweiterung Rot</div>
  <div class="abs product-name" style="left:911px">Jackenerweiterung Blau</div>

  <footer class="abs site-footer">
    <span class="abs" style="left:32px">Unser Newsletter!</span>
    <div class="abs newsletter-input">Deine E-Mail Adresse</div>
    <svg class="abs" style="left:414px;top:16px" width="18" height="18" viewBox="0 0 18 18"><circle cx="9" cy="9" r="9" fill="#f7b3b3"/><path d="M7 5 L12 9 L7 13 Z" fill="#fff"/></svg>
    <div class="abs divider" style="left:448px"></div>
    <div class="abs footer-links"><span>Impressum</span><span>Kontakt</span><span>FAQ</span><span>About</span></div>
    <span class="abs" style="left:855px">(c) 2011 Telvo.de</span>
    <div class="abs divider" style="left:994px"></div>
    <span class="abs" style="left:1006px;font-size:13px">Nach oben</span>
    <svg class="abs" style="left:1078px;top:10px" width="28" height="28" viewBox="0 0 28 28"><circle cx="14" cy="14" r="13" fill="var(--red)" stroke="#f3a0a0"/><path d="M9 16.5 L14 10.5 L19 16.5 Z" fill="#fff"/></svg>
  </footer>
</body>
</html>
```